Companybrochure for Consulting & Financing Firm

I need to have a Company Brochure asap for our company. We have a website that describes what we do, but we need also a brochure, that can be sent by PDF of eventually be printed as well.

The brochure should be short but nice and appealing to the customers.

We provide professional management consulting and help our customers to get finance for very diferent projects. Our business has a lot to do with personal relations, but also we are very professional in the way we work and how develop the solutions for our clients. Our clients are mainly government-owned firm, but also private trading companies and wealthy private investors.

Our customers are mainly in Latin America, but the company is headquater is in Switzerland. We are opening offices in Panama and Caracas, this should be easaly be adabtable later.

Please have a look at our website www.vorelpartners.ch. In the brochure, we would segment our services in 1.) Project Developments 2.) Management Conulting 3.) Investment Management and 4.) Finance Solutions.

Also do have a look at www.vorelpartners.ch
(Click E for the English version)
Updates

I managed to put the Mock-Up to the Website.
It is actually not really a mock-up, it is a version I have designed myself.
Well as I am not a designer, I hope you can make it much better.
The content however is what I would put in any other design as well.

Target Market(s)

Top Management, Investors, Entrepreneurs, Government Officials

Industry/Entity Type

Management Consulting

Requirements
Must have
• Design should reflect this image elements:

We are entrepreneurs.
We are comitted to get things done.
We work closely with the client side by side.
We are a professional partner.
We are not afraid of delivering unconventional solutions.
We look at the problem from various angles.
We analyse, develop solutions and implent results.
Should not have
• Typical US-American style elements. We do not want to give the impression of being a US company.

We do not want to appear to be neo-liberal. We are a politically neutral professional consulting firm.

```html
<!DOCTYPE html>
<html lang="en">
<head>
<meta charset="utf-8">
<title>Vorel Partners – Brochure Spread</title>
<link rel="stylesheet" href="https://fonts.googleapis.com/css2?family=Source+Sans+3:ital,wght@0,400;0,600;0,700;1,400;1,600&display=swap">
<style>
  :root {
    --green: #5f8c20;
    --green-soft: #9bb66b;
    --blue: #07538b;
    --blue-soft: #5a8db8;
    --ink: #1e1e1e;
    --paper: #ffffff;
    --canvas: #ffffff;
    --fold: #a9a9a9;
  }
  * { box-sizing: border-box; margin: 0; padding: 0; }
  html, body {
    width: 1200px; height: 900px; overflow: hidden;
    background: var(--canvas);
    font-family: "Source Sans 3", "Myriad Pro", sans-serif;
    color: var(--ink);
  }
  .stage { position: relative; width: 1200px; height: 900px; }
  .fold-line {
    position: absolute; left: 599px; top: 78px; height: 740px;
    border-left: 1px dashed var(--fold); z-index: 3;
  }
  .spread {
    position: absolute; left: 112px; top: 105px; width: 976px; height: 692px;
    display: flex; box-shadow: 0 0 4px rgba(0,0,0,0.18);
  }
  .page { position: relative; width: 488px; height: 692px; background: var(--paper); }
  .page-header {
    height: 138px; padding: 88px 0 0 46px;
    color: #fff; font-weight: 700; font-size: 16.5px; line-height: 21px;
    letter-spacing: 1.4px; text-transform: uppercase;
  }
  .page--investment .page-header { background: var(--green); }
  .page--finance .page-header { background: var(--blue); }
  .page-body { position: absolute; left: 46px; top: 162px; width: 258px; }
  .lead {
    font-weight: 700; font-size: 11.5px; line-height: 15.5px;
    letter-spacing: 0.3px; text-transform: uppercase; margin-bottom: 13px;
  }
  .page--investment .lead { color: var(--green); }
  .page--finance .lead { color: var(--blue); }
  .body-copy { font-size: 9.6px; line-height: 16px; margin-bottom: 14px; }
  .quote-box {
    position: absolute; left: 325px; top: 163px; width: 116px; height: 225px;
    padding: 12px 10px; color: #fff;
  }
  .page--investment .quote-box { background: var(--green-soft); }
  .page--finance .quote-box { background: var(--blue-soft); }
  .quote-title {
    font-weight: 600; font-size: 10.5px; line-height: 14.5px;
    text-transform: uppercase; letter-spacing: 0.3px; margin-bottom: 6px;
  }
  .quote-text { font-style: italic; font-weight: 600; font-size: 9.6px; line-height: 16px; }
  .photo-rule { position: absolute; left: 0; top: 412px; width: 488px; height: 5px; }
  .page--investment .photo-rule { background: var(--green); }
  .page--finance .photo-rule { background: var(--blue); }
  .photo { position: absolute; left: 0; top: 417px; width: 488px; height: 275px; }
  .photo--meeting {
    background: linear-gradient(100deg, #d9c6ad 0%, #f1e8db 30%, #e6d8c4 55%, #c98a5e 80%, #e9dccb 100%);
  }
  .photo--handshake {
    background: linear-gradient(100deg, #c9b9a9 0%, #f2eeee 28%, #dce6ea 55%, #e8eef0 70%, #2f2b2c 90%, #d9e1e4 100%);
  }
</style>
</head>
<body>
<div class="stage">
  <div class="spread">
    <section class="page page--investment">
      <h2 class="page-header">Investment<br>Management</h2>
      <div class="page-body">
        <p class="lead">Vorel Partners has a clear business-like approach to investments.</p>
        <p class="body-copy">We only engage in those projects or companies with which we have a strong relationship.</p>
        <p class="body-copy">That is why we are also willing to take an entrepreneurial risk in the companies we invest in. We participate with our own capital and assume functions in the company’s management.</p>
        <p class="body-copy">Vorel Partners currently holds shares in seven SMEs; four of these to 100%. Participation is on equal terms, and two of of the companies we are minority shareholders.</p>
      </div>
      <aside class="quote-box">
        <p class="quote-title">What our clients have to say…</p>
        <p class="quote-text">Offesequam, nulla vollaut officte ctatur. sam, es untin pedipid et etur, si aliquatio. Git exerfer erspel int, ut que parunti atures dersped qui quidunt lab ium hit odigenimusam nobis earum, utasi at fugiam quatio berit aut.</p>
      </aside>
      <div class="photo-rule"></div>
      <div class="photo photo--meeting" role="img" aria-label="Photo: a smiling advisor presenting an architectural model to a young couple in a bright room"></div>
    </section>
    <section class="page page--finance">
      <h2 class="page-header">Finance<br>Solutions</h2>
      <div class="page-body">
        <p class="lead">Financing growth opportunities sometimes calls for an entrepreneurial perspective, which is often not found in the traditional banking world.</p>
        <p class="body-copy">That is why we have committed ourselves to developing financing solutions for unconventional requirements. To do so, we often work with partners with complementary subject matter expertise and geographical coverage.</p>
        <p class="body-copy">This gives us the flexibility to create innovative solutions – solutions that meet our clients’ special needs.</p>
      </div>
      <aside class="quote-box">
        <p class="quote-title">What our clients have to say…</p>
        <p class="quote-text">Offesequam, nulla vollaut officte ctatur. sam, es untin pedipid et etur, si aliquatio. Git exerfer erspel int, ut que parunti atures dersped qui quidunt lab ium hit odigenimusam nobis earum, utasi at fugiam quatio berit aut.</p>
      </aside>
      <div class="photo-rule"></div>
      <div class="photo photo--handshake" role="img" aria-label="Photo: a businesswoman holding plans shakes hands with a young couple by a bright window"></div>
    </section>
  </div>
  <div class="fold-line"></div>
</div>
</body>
</html>
```